Creative UI design for web application

I need a new UI design for my web application. It will be used by small and micro business owners to plan & implement growth tactics.

I've attached the current design (which I'm open to be changed) - but in particular I need to design the centre of the screen, where the work actually happens.

There needs to be place for a title (YOUR BUSINESS) and description (say 1-2 paragraphs of text) - and am happy to include icons or imagery where makes sense. It may make sense for the user to be able to upload their business logo and name, for example.

This screen will be used by the business owner to understand the real value they offer potential customers and their point of difference - why they exist and why potential customers should care.

They'll use the information they put into this screen to plan things like their messaging.

Following that, there needs to be 2 sections in the dashboard.

The first section is titled "WHO YOU ARE"

The first section will include a number of boxes that the user can input information into, as follows:

- Logo
- Business name
- Business tag line
- Business vision
- Business bio
- Brand colours (these should end up as swatches based on the colour code they enter) - the colour code for each colour swatch should also be visible.
- Key competitors
- SWOT analysis (boxes to enter their strengths, weaknesses, opportunities and threats).

The second section is titled "WHY YOU EXIST"

The second section will include a number of boxes that the user can input information (text) into, as follows:

- Who are your ideal customers?
- What problem are you trying to solve for them?
- What pain points will this remove for them?
- How do you solve it?
- How else could this problem be solved?
- Who offers these other solutions?
- Why is your solution better?
- How much does your solution cost?
- What value are you providing to justify this cost?
- How will this make their life/job easier/better?

They should be able to write a decent amount of information in the boxes.

There should ideally be a place for a description for each of these text fields (for both section 1 & 2) as well so I can give them a little bit more direction around what to put in the box. Alternatively there could be a little icon (say a question mark or "i") that they could click on to view instructions. The instructions will be around 2-4 sentences long for each text field.

You have 2 options:

a) This all needs to appear on the one screen, and the navigation needs to be visible (as per the example attached but feel free to recreate this navigation)

Note: the page can scroll below the fold - but please provide the design for the full length of the page.

b) Potentially the 2 sections could actually be in 2 different items in the menu - YOUR BUSINESS and YOUR VALUE (which would sit next to YOUR BUSINESS and before YOUR CUSTOMER in the screenshot provided). feel free to design them as 2 separate screens if you prefer.

I have attached a screenshot of the app as it stands today (screen shot 2017) which would still exist in the new design but under a different section (the learn section from the plan2 mockup attached)

I have mocked up how this new screen could look if broken into 2 and that's also attached. If you can make this come to life - and look more engaging that would be helpful! :)

Target Market(s)

Small and micro business owners

Industry/Entity Type

Marketing

Number of Pages Required

1 page

Font styles to use
Sans Serif
Other font styles liked:
• Montserrat

Colors
87cfc6
d2a4cc
ffffff
85cae6
e8e8e8
5c5c5c

Requirements
Must have
• Use of my brand colours: #cc8eb2, #76d6c8, #68c7ff as well as white and #595959. Must be visually pleasing / engaging, designed for desktop (as it's a desktop application), really easy to use / navigate.
• Use font Montserrat light & Montserrat Regular or Bold. Mostly should be Montserrat light.
Nice to have
• Would be nice to see how this would look on mobile (as the application is responsive) but this is not mandatory.
Should not have
• Should not look too corporate or dry.

```html
<!DOCTYPE html>
<html lang="en">
<head>
<meta charset="utf-8">
<title>Seedline – Your Business</title>
<link href="https://fonts.googleapis.com/css2?family=Montserrat:wght@300;400;500;600;700&display=swap" rel="stylesheet">
<style>
:root{
  --bar-dark:#3a3a3a;
  --bar-line:#4a4a4a;
  --sub-bar:#e2e2e2;
  --teal:#76d6c8;
  --pink:#cc8eb2;
  --blue:#68c7ff;
  --text:#595959;
  --text-dark:#3c3c3c;
  --card-bg:#f0f0f0;
  --card-head:#dedede;
  --card-line:#dcdcdc;
  --field-line:#d0d0d0;
  --placeholder:#a8a8a8;
  --footer:#d9d9d9;
  --white:#ffffff;
}
*{box-sizing:border-box;margin:0;padding:0}
html,body{width:1069px;height:1200px;overflow:hidden;background:var(--white)}
body{font-family:'Montserrat',sans-serif;font-weight:300;color:var(--text)}
.page{position:relative;width:1300px;height:1459px;transform:scale(0.82231);transform-origin:0 0}
.topbar{position:absolute;left:0;top:0;width:1300px;height:58px;background:var(--bar-dark)}
.brand{position:absolute;left:20px;top:24px;display:flex;align-items:center;gap:8px;color:var(--white);font-weight:400;font-size:23px;letter-spacing:0.5px}
.brand-dot{width:10px;height:10px;border-radius:50%;background:var(--teal)}
.main-nav{position:absolute;left:245px;top:8px;display:flex;height:50px}
.main-nav a{display:flex;align-items:center;padding:0 20px;color:var(--white);text-decoration:none;font-weight:600;font-size:15px;letter-spacing:0.6px}
.main-nav a.active{background:var(--teal)}
.user-nav{position:absolute;right:0;top:0;height:58px;display:flex}
.user-nav a{display:flex;align-items:center;gap:6px;padding:0 10px;border-left:1px solid var(--bar-line);color:var(--white);text-decoration:none;font-weight:600;font-size:15px}
.user-nav a:last-child{padding-right:36px}
.subbar{position:absolute;left:0;top:58px;width:1300px;height:45px;background:var(--sub-bar);border-bottom:1px solid #d4d4d4}
.sub-nav{position:absolute;left:245px;top:0;display:flex;height:44px}
.sub-nav a{display:flex;align-items:center;padding:0 19px;color:var(--text-dark);text-decoration:none;font-weight:500;font-size:15px;letter-spacing:0.6px;border-right:1px solid #cfcfcf}
.sub-nav a.active{background:var(--pink);color:var(--white);border-right:none}
.intro{position:absolute;left:17px;top:125px;width:1262px;font-size:16px;line-height:24px;letter-spacing:-0.3px}
.intro p+p{margin-top:24px}
.card{position:absolute;background:var(--card-bg);border:1px solid var(--card-line);width:615px}
.card-head{height:50px;background:var(--card-head);padding-left:20px;display:flex;align-items:center;font-weight:600;font-size:21px;letter-spacing:0.8px;color:var(--text-dark)}
.who{left:20px;top:376px;height:1003px}
.why{left:665px;top:376px;height:1003px}
.field{position:absolute;left:19px}
.field label{display:block;font-size:16px;height:20px;line-height:20px;letter-spacing:-0.2px}
.input{position:absolute;height:40px;background:var(--white);border:1px solid var(--field-line);font-size:16px;color:var(--text);padding-left:11px;display:flex;align-items:center}
.btn{position:absolute;height:40px;color:var(--white);display:flex;align-items:center;justify-content:center}
.btn-upload{background:var(--blue);font-size:16px;font-weight:400}
.btn-submit{background:var(--teal);font-size:15px;font-weight:700;letter-spacing:0.8px}
.info{position:absolute;width:21px;height:21px}
.swatch-btn{position:absolute;width:40px;height:40px;background:var(--white);border:1px solid var(--field-line);display:flex;align-items:center;justify-content:center}
.palette{position:absolute;left:26px;top:581px;width:219px;height:120px;background:var(--white);border:1px solid #cfcfcf;box-shadow:0 1px 3px rgba(0,0,0,0.08);z-index:2}
.palette::before{content:"";position:absolute;left:9px;top:-7px;width:12px;height:12px;background:var(--white);border-left:1px solid #cfcfcf;border-top:1px solid #cfcfcf;transform:rotate(45deg)}
.palette-grid{position:absolute;left:11px;top:11px;display:grid;grid-template-columns:repeat(6,28px);grid-auto-rows:28px;gap:6px}
.palette-grid span{border:1px solid #cfcfcf;padding:2px;background:var(--white)}
.palette-grid span i{display:block;width:100%;height:100%}
.brand-swatches{position:absolute;left:262px;top:591px;display:flex;gap:8px}
.brand-swatch{width:105px;height:40px;background:var(--white);border:1px solid var(--field-line);display:flex;align-items:center;gap:8px;padding-left:6px;font-size:13px;font-weight:400;color:var(--text)}
.brand-swatch i{width:26px;height:26px;display:block}
.swot{position:absolute;left:19px;top:767px;width:575px;display:grid;grid-template-columns:1fr 1fr;grid-auto-rows:75px;gap:10px}
.swot-box{background:var(--white);border:1px solid var(--field-line);padding:10px 12px;font-size:14px;color:var(--placeholder);display:flex;gap:8px;align-items:flex-start}
.swot-box b{width:22px;height:22px;flex:none;display:flex;align-items:center;justify-content:center;color:var(--white);font-size:12px;font-weight:700}
.swot-box span{line-height:22px}
.footer{position:absolute;left:0;top:1409px;width:1300px;height:50px;background:var(--footer);display:flex;align-items:center;justify-content:center;font-size:15px;color:var(--text-dark)}
</style>
</head>
<body>
<div class="page">
  <header class="topbar">
    <div class="brand"><span>SEEDLINE</span><span class="brand-dot"></span></div>
    <nav class="main-nav">
      <a class="active" href="#">PLAN</a>
      <a href="#">LEARN</a>
      <a href="#">REMEMBER</a>
    </nav>
    <nav class="user-nav">
      <a href="#"><svg width="16" height="18" viewBox="0 0 16 18" fill="none" stroke="#fff" stroke-width="1.6"><circle cx="8" cy="5.5" r="4"/><path d="M1 17.5c0-4 3-6.5 7-6.5s7 2.5 7 6.5"/></svg>My Profile</a>
      <a href="#"><svg width="20" height="18" viewBox="0 0 20 18" fill="none" stroke="#fff" stroke-width="1.6"><path d="M13 4.5A7.5 7.5 0 1 0 13 13.5"/><path d="M8 9h11M16 6l3 3-3 3"/></svg>Log out</a>
    </nav>
  </header>
  <div class="subbar">
    <nav class="sub-nav">
      <a class="active" href="#">YOUR BUSINESS</a>
      <a href="#">YOUR CUSTOMERS</a>
      <a href="#">YOUR GOALS</a>
      <a href="#">YOUR PLAN</a>
    </nav>
  </div>

  <section class="intro">
    <p>Lorem ipsum dolor sit amet, consectetur adipiscing elit, sed do eiusmod tempor incididunt ut labore et dolore magna aliqua. Ut enim ad minim veniam, quis nostrud exercitation ullamco laboris nisi ut aliquip ex ea commodo consequat. Duis aute irure dolor in reprehenderit in voluptate velit esse cillum dolore eu fugiat nulla pariatur. Excepteur sint occaecat cupidatat non proident, sunt in culpa qui officia deserunt mollit anim id est laborum. Duis aute irure dolor in reprehenderit in voluptate velit esse cillum dolore eu fugiat nulla pariatur. Excepteur sint occaecat cupidatat non proident, sunt in culpa qui officia deserunt mollit anim id est laborum.</p>
    <p>Lorem ipsum dolor sit amet, consectetur adipiscing elit, sed do eiusmod tempor incididunt ut labore et dolore magna aliqua. Ut enim ad minim veniam, quis nostrud exercitation ullamco laboris nisi ut aliquip ex ea commodo consequat. Lorem ipsum dolor sit amet, consectetur adipiscing elit, sed do eiusmod tempor incididunt ut labore et dolore magna aliqua. Ut enim ad minim veniam, quis nostrud exercitation ullamco laboris nisi ut aliquip ex ea commodo consequat.</p>
  </section>

  <section class="card who">
    <h2 class="card-head">WHO YOU ARE</h2>
    <div class="field" style="top:66px"><label>Logo</label></div>
    <div class="input" style="left:19px;top:96px;width:471px"></div>
    <div class="btn btn-upload" style="left:499px;top:96px;width:95px">Upload</div>

    <div class="field" style="top:153px"><label>Business Name</label></div>
    <div class="input" style="left:19px;top:183px;width:575px"></div>

    <div class="field" style="top:240px"><label>Business Tag Line</label></div>
    <div class="input" style="left:19px;top:270px;width:575px"></div>

    <div class="field" style="top:327px"><label>Business Vision</label></div>
    <div class="input" style="left:19px;top:357px;width:575px"></div>

    <div class="field" style="top:414px"><label>Business Bio</label></div>
    <div class="input" style="left:19px;top:444px;width:575px"></div>

    <div class="field" style="top:501px"><label>Brand Colours</label></div>
    <div class="swatch-btn" style="top:531px;left:19px">
      <svg width="22" height="22" viewBox="0 0 22 22">
        <rect x="1" y="1" width="6" height="6" fill="#f4a15c"/><rect x="8" y="1" width="6" height="6" fill="#e76a8f"/><rect x="15" y="1" width="6" height="6" fill="#c46ed1"/>
        <rect x="1" y="8" width="6" height="6" fill="#9fd36a"/><rect x="8" y="8" width="6" height="6" fill="#f2d55b"/><rect x="15" y="8" width="6" height="6" fill="#6a8cf0"/>
        <rect x="1" y="15" width="6" height="6" fill="#58c6a1"/><rect x="8" y="15" width="6" height="6" fill="#6fc6e8"/><rect x="15" y="15" width="6" height="6" fill="#8a7de8"/>
      </svg>
    </div>
    <div class="input" style="left:69px;top:531px;width:525px">#333555</div>
    <div class="palette">
      <div class="palette-grid">
        <span><i style="background:#fb5a5a"></i></span><span><i style="background:#5a72ff"></i></span><span><i style="background:#33f5ff"></i></span><span><i style="background:#66eaa8"></i></span><span><i style="background:#ffff1a"></i></span><span><i style="background:#ffa53a"></i></span>
        <span><i style="background:#ff1f4b"></i></span><span><i style="background:#3e5cff"></i></span><span><i style="background:#00dcf5"></i></span><span><i style="background:#00dc78"></i></span><span><i style="background:#ffe600"></i></span><span><i style="background:#ff8c00"></i></span>
        <span><i style="background:#d90000"></i></span><span><i style="background:#2b4aff"></i></span><span><i style="background:#00b4d8"></i></span><span><i style="background:#00c85a"></i></span><span><i style="background:#ffd200"></i></span><span><i style="background:#ff6a00"></i></span>
      </div>
    </div>
    <div class="brand-swatches">
      <div class="brand-swatch"><i style="background:#333555"></i>#333555</div>
      <div class="brand-swatch"><i style="background:#76d6c8"></i>#76D6C8</div>
      <div class="brand-swatch"><i style="background:#cc8eb2"></i>#CC8EB2</div>
    </div>

    <div class="field" style="top:650px"><label>Key Competitors</label></div>
    <div class="input" style="left:19px;top:680px;width:575px"></div>

    <div class="field" style="top:737px"><label>SWOT Analysis</label></div>
    <div class="swot">
      <div class="swot-box"><b style="background:var(--teal)">S</b><span>Strengths</span></div>
      <div class="swot-box"><b style="background:var(--pink)">W</b><span>Weaknesses</span></div>
      <div class="swot-box"><b style="background:var(--blue)">O</b><span>Opportunities</span></div>
      <div class="swot-box"><b style="background:var(--text)">T</b><span>Threats</span></div>
    </div>

    <div class="btn btn-submit" style="left:470px;top:942px;width:124px">SUBMIT</div>
  </section>

  <section class="card why">
    <h2 class="card-head">WHY YOU EXIST</h2>
    <div class="field" style="top:66px"><label>Who are your ideal customers?</label></div>
    <div class="input" style="left:19px;top:96px;width:545px"></div>
    <div class="field" style="top:153px"><label>What problem are you trying to solve for them?</label></div>
    <div class="input" style="left:19px;top:183px;width:545px"></div>
    <div class="field" style="top:240px"><label>What pain points will this remove for them?</label></div>
    <div class="input" style="left:19px;top:270px;width:545px"></div>
    <div class="field" style="top:327px"><label>How do you solve it?</label></div>
    <div class="input" style="left:19px;top:357px;width:545px"></div>
    <div class="field" style="top:414px"><label>How else could this problem be solved?</label></div>
    <div class="input" style="left:19px;top:444px;width:545px"></div>
    <div class="field" style="top:501px"><label>Who offers these other solutions?</label></div>
    <div class="input" style="left:19px;top:531px;width:545px"></div>
    <div class="field" style="top:588px"><label>Why is your solution better?</label></div>
    <div class="input" style="left:19px;top:619px;width:545px"></div>
    <div class="field" style="top:676px"><label>How much does your solution cost?</label></div>
    <div class="input" style="left:19px;top:707px;width:545px"></div>
    <div class="field" style="top:763px"><label>What value are you providing to justify this cost?</label></div>
    <div class="input" style="left:19px;top:794px;width:545px"></div>
    <div class="field" style="top:851px"><label>How will this make their life/job easier/better?</label></div>
    <div class="input" style="left:19px;top:882px;width:545px"></div>

    <svg class="info" style="left:573px;top:106px" viewBox="0 0 21 21"><circle cx="10.5" cy="10.5" r="10.5" fill="#c4c4c4"/><circle cx="10.5" cy="6" r="1.6" fill="#fff"/><rect x="9.2" y="8.8" width="2.6" height="7.5" rx="1" fill="#fff"/></svg>
    <svg class="info" style="left:573px;top:193px" viewBox="0 0 21 21"><circle cx="10.5" cy="10.5" r="10.5" fill="#c4c4c4"/><circle cx="10.5" cy="6" r="1.6" fill="#fff"/><rect x="9.2" y="8.8" width="2.6" height="7.5" rx="1" fill="#fff"/></svg>
    <svg class="info" style="left:573px;top:280px" viewBox="0 0 21 21"><circle cx="10.5" cy="10.5" r="10.5" fill="#c4c4c4"/><circle cx="10.5" cy="6" r="1.6" fill="#fff"/><rect x="9.2" y="8.8" width="2.6" height="7.5" rx="1" fill="#fff"/></svg>
    <svg class="info" style="left:573px;top:367px" viewBox="0 0 21 21"><circle cx="10.5" cy="10.5" r="10.5" fill="#c4c4c4"/><circle cx="10.5" cy="6" r="1.6" fill="#fff"/><rect x="9.2" y="8.8" width="2.6" height="7.5" rx="1" fill="#fff"/></svg>
    <svg class="info" style="left:573px;top:454px" viewBox="0 0 21 21"><circle cx="10.5" cy="10.5" r="10.5" fill="#c4c4c4"/><circle cx="10.5" cy="6" r="1.6" fill="#fff"/><rect x="9.2" y="8.8" width="2.6" height="7.5" rx="1" fill="#fff"/></svg>
    <svg class="info" style="left:573px;top:541px" viewBox="0 0 21 21"><circle cx="10.5" cy="10.5" r="10.5" fill="#c4c4c4"/><circle cx="10.5" cy="6" r="1.6" fill="#fff"/><rect x="9.2" y="8.8" width="2.6" height="7.5" rx="1" fill="#fff"/></svg>
    <svg class="info" style="left:573px;top:629px" viewBox="0 0 21 21"><circle cx="10.5" cy="10.5" r="10.5" fill="#c4c4c4"/><circle cx="10.5" cy="6" r="1.6" fill="#fff"/><rect x="9.2" y="8.8" width="2.6" height="7.5" rx="1" fill="#fff"/></svg>
    <svg class="info" style="left:573px;top:716px" viewBox="0 0 21 21"><circle cx="10.5" cy="10.5" r="10.5" fill="#c4c4c4"/><circle cx="10.5" cy="6" r="1.6" fill="#fff"/><rect x="9.2" y="8.8" width="2.6" height="7.5" rx="1" fill="#fff"/></svg>
    <svg class="info" style="left:573px;top:804px" viewBox="0 0 21 21"><circle cx="10.5" cy="10.5" r="10.5" fill="#c4c4c4"/><circle cx="10.5" cy="6" r="1.6" fill="#fff"/><rect x="9.2" y="8.8" width="2.6" height="7.5" rx="1" fill="#fff"/></svg>
    <svg class="info" style="left:573px;top:891px" viewBox="0 0 21 21"><circle cx="10.5" cy="10.5" r="10.5" fill="#c4c4c4"/><circle cx="10.5" cy="6" r="1.6" fill="#fff"/><rect x="9.2" y="8.8" width="2.6" height="7.5" rx="1" fill="#fff"/></svg>

    <div class="btn btn-submit" style="left:470px;top:942px;width:124px">SUBMIT</div>
  </section>

  <footer class="footer">Copyright © 2017 Seedline.</footer>
</div>
</body>
</html>
```